Building company buisness cards

We are looking for a sharp modern new look for our business cards.
We are a New Zealand based company that specialises in house and land packages.
We have attached a photo of the current logo and would like to see if it can be improved somehow if needed.
We are open to any colours but we have chosen green at this stage.
Feel free to change the font and make the logo smarter looking.
Play with the colours and see what looks best.

We want a card that looks so good know one will want to throw it away!

Target Market(s)

Home buyers

Industry/Entity Type

Building

Contact Information for Business Card

Derek Tolvane
0217394062
dtolvane@quillmarkhomesteads.co.nz
quillmarkhomesteads.co.nz

Font styles to use
Serif
Sans Serif

Colors

Designer to choose colors to be used in the design.

Requirements
Must have
• Logo and company name on one side, details on the other side
Nice to have
• Color codes for the original green are HEX #4a8028, RGB(74,128,40), CMYK(42,0,69,50)
• Round corners, Raised and/or spot UV

```html
<!DOCTYPE html>
<html lang="en">
<head>
<meta charset="utf-8">
<title>Quillmark Homesteads – Business Cards</title>
<link href="https://fonts.googleapis.com/css2?family=Open+Sans:wght@400;600;800&display=swap" rel="stylesheet">
<style>
  :root {
    --backdrop: #3a322e;
    --card: #1f2122;
    --card-edge: #2a2c2d;
    --green: #4a9a2c;
    --silver: #b9bcbe;
    --ink: #f2f2f2;
    --rule: #e6e6e6;
  }
  * { box-sizing: border-box; margin: 0; padding: 0; }
  html, body { width: 1200px; height: 864px; overflow: hidden; }
  body {
    background: var(--backdrop);
    font-family: "Open Sans", sans-serif;
    position: relative;
  }
  .card {
    position: absolute;
    width: 560px;
    height: 312px;
    background: var(--card);
    border: 1px solid var(--card-edge);
    border-radius: 8px;
    box-shadow: 0 14px 30px rgba(0,0,0,.45);
    overflow: hidden;
  }
  /* Front: brand side */
  .card--front { left: 40px; top: 60px; }
  .front__brand {
    position: absolute;
    left: 0; right: 0; top: 110px;
    text-align: center;
    color: var(--silver);
    font-weight: 800;
    font-size: 30px;
    letter-spacing: .5px;
    line-height: 1;
  }
  .front__url {
    position: absolute;
    left: 0; right: 0; top: 200px;
    text-align: center;
    color: var(--silver);
    font-size: 15px;
    letter-spacing: 2.4px;
  }
  /* Back: details side */
  .card--back { left: 600px; top: 490px; }
  .back__name {
    position: absolute;
    left: 36px; top: 64px;
    color: var(--green);
    font-weight: 800;
    font-size: 20px;
    text-transform: uppercase;
    letter-spacing: .3px;
  }
  .back__rule-top {
    position: absolute;
    left: 36px; top: 98px;
    width: 270px; height: 1px;
    background: var(--rule);
  }
  .back__contacts {
    position: absolute;
    left: 36px; top: 110px;
    list-style: none;
    color: var(--ink);
    font-size: 15px;
    line-height: 22px;
  }
  .back__contacts li { display: flex; align-items: center; gap: 10px; }
  .back__contacts svg { width: 12px; height: 12px; flex: none; }
  .back__rule-bottom {
    position: absolute;
    left: 36px; right: 36px; top: 250px;
    height: 1px;
    background: var(--rule);
  }
  .back__brand {
    position: absolute;
    right: 34px; top: 62px;
    display: flex; align-items: center; gap: 10px;
    color: var(--green);
    font-weight: 800;
    font-size: 24px;
    line-height: 1;
  }
  .back__brand-dot {
    width: 12px; height: 12px;
    background: var(--green);
  }
</style>
</head>
<body>

  <section class="card card--front" aria-label="Card front">
    <div class="front__brand">quillmark homesteads</div>
    <div class="front__url">www.quillmarkhomesteads.co.nz</div>
  </section>

  <section class="card card--back" aria-label="Card back">
    <div class="back__brand"><span class="back__brand-dot"></span>quillmark homesteads</div>

    <h1 class="back__name">Derek Tolvane</h1>
    <div class="back__rule-top"></div>

    <ul class="back__contacts">
      <li>
        <svg viewBox="0 0 12 12" aria-hidden="true"><path fill="#4a9a2c" d="M2.5 1h2l1 2.6-1.3.9a6 6 0 0 0 3.3 3.3l.9-1.3 2.6 1v2a1.2 1.2 0 0 1-1.3 1.2A9.8 9.8 0 0 1 1.3 2.3 1.2 1.2 0 0 1 2.5 1z"/></svg>
        0217394062
      </li>
      <li>
        <svg viewBox="0 0 12 12" aria-hidden="true"><rect x="0.5" y="2" width="11" height="8" fill="#4a9a2c"/><path d="M1 2.5 6 6.5l5-4" fill="none" stroke="#1f2122" stroke-width="1.2"/></svg>
        dtolvane@quillmarkhomesteads.co.nz
      </li>
      <li>
        <svg viewBox="0 0 12 12" aria-hidden="true"><circle cx="6" cy="6" r="5.5" fill="#4a9a2c"/><path d="M.5 6h11M6 .5c-3 3-3 8 0 11M6 .5c3 3 3 8 0 11" fill="none" stroke="#1f2122" stroke-width=".9"/></svg>
        quillmarkhomesteads.co.nz
      </li>
    </ul>

    <div class="back__rule-bottom"></div>
  </section>

</body>
</html>
```